Quorva - corporate Business Card

We need a good look and innovative business card for a new start up company based in Los Angeles called "Quorva". We are in a payment business, including payment card, app, and ewallet. We are expert in online payment and Card not present (CNP) transaction.
We need an innovative, modern business card.

Our logo font is Aero Matics

Target Market(s)

Startup - Bank - Online Payment - Card Manufacturing

Industry/Entity Type

Startup

Contact Information for Business Card

phone: 555 014 7396 - Address: 4172 Marlowe blvd, Brenmoor Heights, CA 90299

Requirements
Must have
• Message: innovative, professional, expert, high tech, trust, online payment expert, security
Nice to have
• no comment
Should not have
• no Comment

```html
<!DOCTYPE html>
<html lang="en">
<head>
<meta charset="utf-8">
<title>Quorva – Business Card</title>
<link rel="stylesheet" href="https://fonts.googleapis.com/css2?family=Exo+2:wght@500&family=Roboto:wght@400;500&display=swap">
<style>
  :root {
    --backdrop: #2b2b2d;
    --brand-red: #b81d2f;
    --card-white: #ffffff;
    --ink-white: #ffffff;
    --ink-soft: #f6dde0;
  }
  * { box-sizing: border-box; margin: 0; padding: 0; }
  html, body {
    width: 1200px; height: 950px; overflow: hidden;
    background: var(--backdrop);
  }
  .canvas {
    width: 1200px; height: 950px;
    display: flex; flex-direction: column; align-items: center; justify-content: center;
    gap: 60px;
  }
  .card {
    width: 700px; height: 400px;
    position: relative;
    box-shadow: 0 10px 28px rgba(0,0,0,0.45);
  }
  .card--front { background: var(--brand-red); color: var(--ink-white); }
  .card--back {
    background: var(--card-white);
    display: flex; align-items: center; justify-content: center; gap: 22px;
  }
  .wordmark {
    font-family: "Exo 2", sans-serif;
    font-weight: 500;
    letter-spacing: 1px;
    line-height: 1;
  }
  .card--front .wordmark {
    position: absolute; left: 44px; top: 50px;
    font-size: 74px; color: var(--ink-white);
  }
  .card--back .wordmark { font-size: 96px; color: var(--brand-red); }
  .brand-dot {
    width: 104px; height: 104px; border-radius: 50%;
    background: var(--brand-red);
  }
  .person {
    position: absolute; left: 48px; top: 168px;
    font-family: "Roboto", sans-serif;
  }
  .person__name { font-size: 22px; font-weight: 500; }
  .person__role { font-size: 15px; color: var(--ink-soft); margin-top: 3px; }
  .contact {
    position: absolute; left: 48px; top: 250px;
    font-family: "Roboto", sans-serif; font-size: 14px; line-height: 1.45;
    list-style: none;
  }
  .contact__address { margin-bottom: 6px; }
  .contact__row { display: flex; align-items: center; gap: 9px; }
  .contact__icon { width: 13px; height: 13px; flex: none; }
</style>
</head>
<body>
<main class="canvas">
  <section class="card card--front" aria-label="Card front">
    <h1 class="wordmark">Quorva</h1>
    <div class="person">
      <p class="person__name">Dana Reyes</p>
      <p class="person__role">President</p>
    </div>
    <ul class="contact">
      <li class="contact__address">4172 Marlowe blvd<br>Brenmoor Heights, CA 90299</li>
      <li class="contact__row">
        <svg class="contact__icon" viewBox="0 0 16 16" aria-hidden="true"><path fill="#fff" d="M3.5 1.5l3 3-1.7 1.7a9 9 0 0 0 5 5l1.7-1.7 3 3-2 2C7 14 2 9 1.5 3.5z"/></svg>
        <span>555 014 7396</span>
      </li>
      <li class="contact__row">
        <svg class="contact__icon" viewBox="0 0 16 16" aria-hidden="true"><rect x="1" y="3" width="14" height="10" fill="#fff"/><path d="M1 3l7 6 7-6" fill="none" stroke="#b81d2f" stroke-width="1.4"/></svg>
        <span>dana@quorva.com</span>
      </li>
      <li class="contact__row">
        <svg class="contact__icon" viewBox="0 0 16 16" aria-hidden="true"><circle cx="8" cy="8" r="7" fill="#fff"/><path d="M1 8h14M8 1c-3 4-3 10 0 14M8 1c3 4 3 10 0 14" fill="none" stroke="#b81d2f" stroke-width="1"/></svg>
        <span>www.quorva.com</span>
      </li>
    </ul>
  </section>

  <section class="card card--back" aria-label="Card back">
    <span class="brand-dot" aria-hidden="true"></span>
    <p class="wordmark">Quorva</p>
  </section>
</main>
</body>
</html>
```